EB-5 Regional Center needs a Web design

Harlow Ridge Financial Partners is an expanding EB-r regional center. We have been successful in sponsoring multiple projects of third-party developers and placing EB-5, B-1, and Private Investments into multiple projects.

We are now partnering directly with project developers in the energy and healthcare to raise foreign capital for projects in those industries. The foreign capital is used as project equity and our collective balance sheets are used to guarantee debt to complete the funding of the projects.

We need a web site where we can post our company credentials, the bios of each partner, a document page for each of our projects where we can post specific project related documents which foreign investors can read, and we will need a section where foreign investors can fill out investor forms confirming that they are qualified investors and leaving their contact so that our agents and executives can make contact.

The final design should reflect the exceptional experience of the partners and our financial strength and stability.

We do have a logo we would want to use on the web design.

Target Market(s)

EB-5 Investors, B-1 Investors, Private Equity and other investors seeking quality investment in job creating US projects.

Coding

Number of Pages Required

5+ page

Font styles to use
Sans Serif

Requirements
Must have
• Pages to display company info, partner bios, projects completed, and a projects in-process page where we can post documents and info on projects for which we are seeking foreign investment. We also need a section where investors can enter their qualifying personal information and leave contact information for us.

```html
<!DOCTYPE html>
<html lang="en">
<head>
<meta charset="utf-8">
<title>Harlow Ridge Financial Partners</title>
<link href="https://fonts.googleapis.com/css2?family=Lato:wght@400;700;900&family=Montserrat:wght@600;700;800&display=swap" rel="stylesheet">
<style>
:root{
  --ink:#222;
  --text:#555;
  --grey:#6d6d6d;
  --grey-dark:#4a4a4a;
  --light:#f1f1f1;
  --panel:#e9e9e9;
  --footer:#2f2f2f;
  --white:#fff;
  --line:#777;
}
*{box-sizing:border-box;margin:0;padding:0}
html,body{width:1200px;height:3862px;overflow:hidden}
body{position:relative;font-family:'Lato',sans-serif;color:var(--text);background:var(--white)}
.abs{position:absolute}
.section{position:absolute;left:0;width:1200px;overflow:hidden}
.heading{font-family:'Montserrat',sans-serif;font-weight:700;color:var(--ink);font-size:34px;letter-spacing:1px;text-align:center;position:absolute;left:0;width:1200px}
.rule{position:absolute;left:570px;width:60px;height:3px;background:var(--line)}
.btn{position:absolute;display:flex;align-items:center;justify-content:center;gap:8px;border-radius:26px;background:var(--grey);color:var(--white);font-family:'Lato',sans-serif;font-weight:700;font-size:14px;text-transform:uppercase}
.btn .dot{width:13px;height:13px;border-radius:50%;background:var(--white);display:inline-flex;align-items:center;justify-content:center}
.btn .dot:after{content:"";border-left:5px solid var(--grey);border-top:3.5px solid transparent;border-bottom:3.5px solid transparent;margin-left:2px}
.btn.outline{background:transparent;border:2px solid var(--white)}
.btn.outline .dot:after{border-left-color:#8a8a8a}
.arrow{position:absolute;width:40px;height:40px;border-radius:50%;border:1.5px solid #444;background:rgba(255,255,255,.6);display:flex;align-items:center;justify-content:center}

/* header */
.site-header{top:0;height:84px;background:var(--white);z-index:3}
.brand{left:112px;top:18px;display:flex;align-items:center;gap:12px}
.brand-mark{width:40px;height:40px;border-radius:50%;background:var(--grey)}
.brand-name{font-family:'Lato',sans-serif;font-weight:700;color:var(--grey);font-size:19px;line-height:22px;letter-spacing:.5px}
.nav{left:466px;top:36px;display:flex;gap:28px;font-size:14px;font-weight:700;color:var(--ink)}
.nav span.active{border-bottom:3px solid var(--grey);padding-bottom:9px}
.login{left:966px;top:21px;width:123px;height:49px;font-size:14px}

/* hero */
.hero{top:84px;height:557px;background:linear-gradient(100deg,#b9a898 0%,#8f8378 30%,#c3bcb4 55%,#d7d2cc 80%,#9d948b 100%)}
.hero-photo{position:absolute;inset:0}
.hero-shade{position:absolute;left:603px;top:0;width:597px;height:557px;background:rgba(255,255,255,.15)}
.hero-title{top:150px;left:0;width:1200px;text-align:center;font-family:'Montserrat',sans-serif;color:var(--white);font-weight:800;font-size:62px;letter-spacing:2px;line-height:64px}
.hero-sub{top:214px;left:0;width:1200px;text-align:center;color:var(--white);font-family:'Montserrat',sans-serif;font-weight:600;font-size:38px}
.hero-text{top:288px;left:0;width:1200px;text-align:center;color:var(--white);font-size:14px}

/* about */
.about{top:641px;height:587px;background:var(--white)}
.about p{position:absolute;left:200px;width:800px;top:210px;text-align:center;font-size:14px;line-height:30px;color:var(--text)}

/* projects */
.projects{top:1228px;height:839px;background:linear-gradient(180deg,#ececec,#e2e2e2)}
.tabs{position:absolute;top:155px;left:154px;display:flex;gap:7px}
.tab{width:173px;height:52px;background:var(--white);display:flex;align-items:center;justify-content:center;font-size:14px;font-weight:700;color:var(--ink);box-shadow:0 1px 3px rgba(0,0,0,.1)}
.tab.active{background:var(--grey);color:var(--white)}
.tile{position:absolute;width:315px;height:222px;border:3px solid var(--white);box-shadow:0 1px 4px rgba(0,0,0,.15)}
.tile.t1{background:linear-gradient(135deg,#cfc6bb,#9a8670)}
.tile.t2{background:linear-gradient(135deg,#dcdad6,#6e7682)}
.tile.t3{background:linear-gradient(135deg,#ecebea,#8e8a86)}
.tile.t4{background:linear-gradient(135deg,#5b6f86,#c9ced6)}
.tile.t5{background:linear-gradient(135deg,#7c7c7c,#4c4c4c)}
.tile.t6{background:linear-gradient(135deg,#b7b3ac,#5f6873)}
.tile-overlay{position:absolute;inset:8px;border:2px solid var(--white);display:flex;flex-direction:column;align-items:center;justify-content:center;color:var(--white);text-align:center}
.tile-overlay b{font-size:14px;margin-bottom:6px}
.tile-overlay span{font-size:13.5px;line-height:19px;width:200px}

/* partners */
.partners{top:2067px;height:625px;background:var(--white)}
.card{position:absolute;top:206px;width:238px;height:310px;background:var(--white);box-shadow:0 1px 5px rgba(0,0,0,.18);border-bottom:3px solid #8a8a8a}
.card .photo{position:absolute;left:6px;top:6px;width:226px;height:212px;background:linear-gradient(180deg,#f1f1f1,#dcdcdc)}
.card .name{position:absolute;top:246px;left:0;width:100%;text-align:center;font-size:14px;font-weight:700;color:var(--ink)}
.card .role{position:absolute;top:266px;left:0;width:100%;text-align:center;font-size:14px;color:var(--text)}
.card.hover{background:#7d7d7d}
.card.hover .name,.card.hover .role{color:#eaeaea}
.social{position:absolute;left:14px;width:28px;height:28px;background:#888;border:1px solid #bbb}

/* media + contact */
.split{top:2692px;height:515px}
.media{left:0;top:0;width:588px;height:515px;background:linear-gradient(135deg,#8c8c8c,#6a6a6a)}
.contact{left:588px;top:0;width:612px;height:515px;background:linear-gradient(135deg,#5f5f5f,#4e4e4e)}
.light-title{font-family:'Montserrat',sans-serif;font-weight:700;color:#ececec;text-align:center;position:absolute}
.field{position:absolute;background:var(--white);border:1px solid #ddd;font-size:14px;color:#666;padding:14px 18px}

/* testimonial */
.testimonial{top:3207px;height:339px;background:linear-gradient(180deg,#f6f6f6,#eeeeee)}
.quote{position:absolute;left:240px;width:720px;top:146px;text-align:center;font-family:Arial,sans-serif;font-size:14.5px;line-height:31px;color:var(--text)}
.qmark{position:absolute;font-family:Georgia,serif;font-size:60px;color:#777;line-height:1}

/* footer */
.footer{top:3546px;height:316px;background:var(--footer)}
.links{position:absolute;top:211px;left:0;width:1200px;display:flex;justify-content:center;gap:22px;color:#eee;font-size:14.5px}
</style>
</head>
<body>

<header class="section site-header">
  <div class="abs brand">
    <span class="brand-mark"></span>
    <span class="brand-name">HARLOW RIDGE<br>Financial Partners</span>
  </div>
  <nav class="abs nav">
    <span class="active">HOME</span><span>ABOUT US</span><span>RECENT PROJECTS</span><span>PARTNER BIO</span>
  </nav>
  <div class="btn login">LOG IN
    <svg width="10" height="12" viewBox="0 0 10 12"><rect x="0" y="5" width="10" height="7" fill="#fff"/><path d="M2 5V3.5a3 3 0 0 1 6 0V5" stroke="#fff" stroke-width="1.6" fill="none"/></svg>
  </div>
</header>

<section class="section hero">
  <div class="hero-photo" role="img" aria-label="Photo of hands signing documents at a desk"></div>
  <div class="hero-shade"></div>
  <h1 class="abs hero-title">HARLOW RIDGE</h1>
  <div class="abs hero-sub">Financial Partners</div>
  <p class="abs hero-text">Lorem ipsum dolor sit amet, consectetur adipiscing elit, sed do eiusmod tempor incididunt ut labore</p>
  <div class="btn" style="left:412px;top:341px;width:158px;height:48px">Get Started <span class="dot"></span></div>
  <div class="btn outline" style="left:642px;top:341px;width:160px;height:48px">Contact Us <span class="dot"></span></div>
  <div class="arrow" style="left:42px;top:258px"><svg width="12" height="14" viewBox="0 0 12 14"><path d="M9 1 3 7l6 6" stroke="#222" stroke-width="2" fill="none"/></svg></div>
  <div class="arrow" style="left:1124px;top:258px"><svg width="12" height="14" viewBox="0 0 12 14"><path d="M3 1l6 6-6 6" stroke="#222" stroke-width="2" fill="none"/></svg></div>
</section>

<section class="section about">
  <h2 class="heading" style="top:118px">ABOUT US</h2>
  <div class="rule" style="top:170px"></div>
  <p>Sed ut perspiciatis unde omnis iste natus error sit voluptatem accusantium doloremque laudantium, totam rem aperiam, eaque ipsa quae ab illo inventore veritatis et quasi architecto beatae vitae dicta sunt explicabo. Nemo enim ipsam voluptatem quia voluptas sit aspernatur aut odit aut fugit, sed quia consequuntur magni dolores eos qui ratione voluptatem sequi nesciunt. Neque porro quisquam est, qui dolorem ipsum. quia dolor sit amet, consectetur, adipisci velit, sed quia non numquam eius modi tempora incidunt ut labore et dolore magnam aliquam quaerat Sed ut perspiciatis unde omnis iste natus error sit voluptatem accusantium doloremque laudantium.</p>
  <div class="btn" style="left:520px;top:426px;width:160px;height:49px">Read More <span class="dot"></span></div>
</section>

<section class="section projects">
  <h2 class="heading" style="top:62px">RECENT PROJECTS</h2>
  <div class="rule" style="top:112px"></div>
  <div class="tabs">
    <div class="tab active">ALL PROJECTS</div><div class="tab">CORPORATE</div><div class="tab">BUSINESS</div><div class="tab">ENTERTAINMENT</div><div class="tab">INNOVATIONS</div>
  </div>
  <div class="tile t1" style="left:114px;top:302px" role="img" aria-label="Photo of a team meeting around a laptop"></div>
  <div class="tile t2" style="left:442px;top:302px" role="img" aria-label="Photo of colleagues shaking hands at a table"></div>
  <div class="tile t3" style="left:770px;top:302px" role="img" aria-label="Photo of a consultant presenting charts"></div>
  <div class="tile t4" style="left:114px;top:539px" role="img" aria-label="Photo of financial charts on a desk"></div>
  <div class="tile t5" style="left:442px;top:539px" role="img" aria-label="Photo of a keyboard and paperwork">
    <div class="tile-overlay">
      <b>LOREM IPSUM DOLOR</b>
      <span>Sed ut perspiciatis unde omnis iste natus error sit</span>
      <svg width="18" height="18" viewBox="0 0 18 18" style="margin-top:8px"><circle cx="7.5" cy="7.5" r="5.5" stroke="#fff" stroke-width="2" fill="none"/><path d="M11.5 11.5 16 16M5 7.5h5M7.5 5v5" stroke="#fff" stroke-width="2"/></svg>
    </div>
  </div>
  <div class="tile t6" style="left:770px;top:539px" role="img" aria-label="Photo of an advisor reviewing documents with clients"></div>
</section>

<section class="section partners">
  <h2 class="heading" style="top:106px">PARTNER BIOS</h2>
  <div class="rule" style="top:157px"></div>
  <div class="card" style="left:111px"><div class="photo" role="img" aria-label="Portrait of a partner"></div><div class="name">DANIEL ROURKE</div><div class="role">Businessman</div></div>
  <div class="card hover" style="left:358px"><div class="photo" role="img" aria-label="Portrait of a partner"></div>
    <span class="social" style="top:16px"></span><span class="social" style="top:50px"></span><span class="social" style="top:84px"></span>
    <div class="name">DANIEL ROURKE</div><div class="role">Businessman</div></div>
  <div class="card" style="left:605px"><div class="photo" role="img" aria-label="Portrait of a partner"></div><div class="name">DANIEL ROURKE</div><div class="role">Businessman</div></div>
  <div class="card" style="left:852px"><div class="photo" role="img" aria-label="Portrait of a partner"></div><div class="name">DANIEL ROURKE</div><div class="role">Businessman</div></div>
</section>

<section class="section split">
  <div class="abs media" role="img" aria-label="Faded photo of a desk with laptop and notebook">
    <div class="light-title" style="left:0;top:63px;width:588px;font-size:30px;line-height:37px">OUR WORK PROCESS<br>AS VIDEOS</div>
    <div class="abs" style="left:266px;top:155px;width:56px;height:3px;background:#ddd"></div>
    <p class="abs" style="left:0;top:186px;width:596px;text-align:center;color:#eee;font-size:14px">Lorem ipsum dolor sit amet, consectetur adipiscing elit</p>
    <svg class="abs" style="left:268px;top:241px" width="56" height="56" viewBox="0 0 56 56"><circle cx="28" cy="28" r="26" stroke="#eee" stroke-width="2.5" fill="none"/><path d="M22 18v20l16-10z" fill="#eee"/></svg>
    <div class="btn" style="left:218px;top:324px;width:159px;height:49px;background:#5c5c5c">View More <span class="dot"></span></div>
  </div>
  <div class="abs contact">
    <div class="light-title" style="left:0;top:70px;width:612px;font-size:33px">GET IN TOUCH</div>
    <div class="abs" style="left:278px;top:127px;width:56px;height:3px;background:#ddd"></div>
    <div class="field" style="left:82px;top:156px;width:216px;height:47px">First Name</div>
    <div class="field" style="left:309px;top:156px;width:216px;height:47px">Last Name</div>
    <div class="field" style="left:82px;top:214px;width:216px;height:47px">Email</div>
    <div class="field" style="left:309px;top:214px;width:216px;height:47px">Phone no</div>
    <div class="field" style="left:82px;top:275px;width:442px;height:79px">Message</div>
    <div class="btn" style="left:224px;top:388px;width:159px;height:48px;background:#8a8a8a">Submit Now <span class="dot"></span></div>
  </div>
</section>

<section class="section testimonial">
  <h2 class="heading" style="top:62px;font-size:30px">WHAT OUR CLIENT SAYS</h2>
  <div class="rule" style="top:107px"></div>
  <span class="qmark" style="left:214px;top:124px">&ldquo;</span>
  <p class="quote">Dr. Castellan is respectful, conducts the imaging in a professional environment, and explains the process step by step. He is knowledgeable, informative, and available to answer any questions during the exam, and as follow up after you receive your report.</p>
  <span class="qmark" style="left:936px;top:190px">&rdquo;</span>
  <div class="abs" style="left:470px;top:246px;width:48px;height:48px;border-radius:50%;background:linear-gradient(135deg,#d89a6a,#a85a34)" role="img" aria-label="Client portrait"></div>
  <div class="abs" style="left:536px;top:262px;font-size:14px;font-weight:700;color:var(--ink)">ELENA MARSH WHITFORD</div>
  <div class="arrow" style="left:36px;top:169px"><svg width="12" height="14" viewBox="0 0 12 14"><path d="M9 1 3 7l6 6" stroke="#222" stroke-width="2" fill="none"/></svg></div>
  <div class="arrow" style="left:1124px;top:169px"><svg width="12" height="14" viewBox="0 0 12 14"><path d="M3 1l6 6-6 6" stroke="#222" stroke-width="2" fill="none"/></svg></div>
</section>

<footer class="section footer">
  <div class="abs" style="left:207px;top:52px;font-size:25px;font-weight:700;color:#f2f2f2">Join Our Newsletter</div>
  <div class="abs" style="left:547px;top:51px;width:487px;height:46px;background:var(--white);border:2px solid #ccc;display:flex;align-items:center;padding-left:20px;gap:14px;font-size:15px;color:#555">
    <svg width="18" height="13" viewBox="0 0 18 13"><rect x="1" y="1" width="16" height="11" stroke="#888" stroke-width="1.4" fill="none"/><path d="M1 1l8 6 8-6" stroke="#888" stroke-width="1.4" fill="none"/></svg>
    Email
  </div>
  <div class="abs" style="left:893px;top:51px;width:141px;height:46px;background:#777;border:2px solid #ccc;display:flex;align-items:center;justify-content:center;color:#fff;font-weight:700;font-size:16px">SUBSCRIBE</div>
  <div class="abs" style="left:111px;top:154px;width:978px;height:1px;background:#777"></div>
  <div class="links"><span>Home</span><span>|</span><span>About Us</span><span>|</span><span>Our Services</span><span>|</span><span>Careers</span><span>|</span><span>Contact Us</span></div>
  <div class="abs" style="left:0;top:262px;width:1200px;text-align:center;color:#eee;font-size:14.5px">&copy; 2020 Harlow Ridge Financial Partners. All Rights Reserved</div>
</footer>

</body>
</html>
```